Website 950x200 Header w/ logo

I'm in need of a website header for a new site called DaysofMarlo.com

The site is basically a glorified blog for myself to write my thoughts about politics, sports, TV shows, current events, whatever. I have a lot of interests.

The site is going to look very very similar to http://www.brisknetmaker.example/4093817/8-ways-to-win-the-race-for-creative-talent

but instead of having a dynamic header that becomes the picture with each article, its just going to be a static header in which I'd like to have the name of the site (Days of Marlo) and some kind of logo, pictures, etc - I'm totally open to anything. The only thing is it needs to have a dark (probably black) background and needs to be 950x200px.

I envision a black background, with gray and white as the primary colors and then some secondary colors potentially, but again I'm open to anything as long as it's on the black background or some kind of charcoal gray or wahtever. On the site the black part will go all the way from the left of the screen to the right no matter what the window size, but I'd like to keep all the content inside of 950x200px

email me marlo.pettigrew@inboxly.example if you have any questions. Thanks!

Industry/Entity Type

Tv

```html
<!DOCTYPE html>
<html lang="en">
<head>
<meta charset="utf-8">
<title>Days of Marlo — Header</title>
<link rel="stylesheet" href="https://fonts.googleapis.com/css2?family=Cinzel:wght@400&family=Open+Sans:wght@400&display=swap">
<style>
  :root {
    --page-white: #ffffff;
    --band-top: #3b3b3b;
    --band-mid: #1a1a1a;
    --band-bottom: #000000;
    --title-grey: #6f7174;
    --title-edge: #c9cbcd;
    --mark-white: #f2f2f2;
    --url-grey: #a9a9a9;
    --ring-silver: rgba(200, 200, 200, 0.16);
  }
  html, body {
    margin: 0;
    padding: 0;
    width: 1200px;
    height: 333px;
    overflow: hidden;
    background: var(--page-white);
  }
  .header-canvas {
    position: relative;
    width: 1200px;
    height: 333px;
    background: var(--page-white);
  }
  .header-band {
    position: absolute;
    left: 0;
    top: 37px;
    width: 1200px;
    height: 296px;
    background: linear-gradient(180deg, var(--band-top) 0%, var(--band-mid) 45%, var(--band-bottom) 100%);
    overflow: hidden;
  }
  .oval-ring {
    position: absolute;
    left: 27px;
    top: 52px;
    width: 1160px;
    height: 230px;
    border-radius: 50%;
    background: radial-gradient(ellipse at center,
      transparent 0%, transparent 58%,
      var(--ring-silver) 72%, var(--ring-silver) 82%,
      transparent 96%);
  }
  .site-mark {
    position: absolute;
    left: 44px;
    top: 40px;
    width: 150px;
    font-family: "Cinzel", serif;
    font-weight: 400;
    font-size: 26px;
    line-height: 1.15;
    color: var(--mark-white);
  }
  .site-title {
    position: absolute;
    left: 0;
    top: 120px;
    width: 1200px;
    margin: 0;
    text-align: center;
    font-family: "Cinzel", serif;
    font-weight: 400;
    font-size: 50px;
    letter-spacing: 2px;
    color: var(--title-grey);
    -webkit-text-stroke: 0.6px var(--title-edge);
  }
  .site-url {
    position: absolute;
    left: 10px;
    top: 212px;
    margin: 0;
    font-family: "Open Sans", sans-serif;
    font-weight: 400;
    font-size: 32px;
    color: var(--url-grey);
  }
</style>
</head>
<body>
  <div class="header-canvas">
    <header class="header-band">
      <div class="oval-ring" role="img" aria-label="Ring of scattered silver and grey ovals circling the title"></div>
      <div class="site-mark">Days of<br>Marlo</div>
      <h1 class="site-title">DAYS OF MARLO</h1>
      <p class="site-url">DaysofMarlo.com</p>
    </header>
  </div>
</body>
</html>
```